Website Redesign Project Puzzle Vault Larkfield

We are an escape room company located in Ashburn, Virginia. We currently have a website https://www.puzzlevaultlarkfield.example based upon html/bootstrap/javascript/php/mysql and I'd like to keep it that way. I'm looking for someone upgrade the front page so it is more informative, cleaner, quicker to load, and optimizes the space for full sale opportunities.

Target Market(s)

Corporate Clients, Families, Friends. All ages

Industry/Entity Type

Entertainment Industry

Coding

Coded - Design and coding required

Number of Pages Required

3 page

Font styles to use
Other font styles liked:
• Similar to Facebook or Amazon

Requirements
Must have
• Must be mobile friendly. bootstrap. Lots of graphics (will provide) nice and easy to read fonts. Easy to read layout. Must look clean, fresh, exciting, and want to grab attention.
• Please visit my facebook page and website for more details. facebook.com/puzzlevaultlarkfield
Nice to have
• Same color as existing but open to options if they look nice.
Should not have
• Should not be wordpress or hard to modify.

```html
<!DOCTYPE html>
<html lang="en">
<head>
<meta charset="utf-8">
<title>Puzzle Vault Larkfield</title>
<link rel="stylesheet" href="https://fonts.googleapis.com/css2?family=Montserrat:wght@400;600;700&family=Open+Sans:wght@300;400;600;700&display=swap">
<style>
:root{
  --accent:#1ba8df;
  --accent-dark:#128cbc;
  --heading:#1fa9cf;
  --ink:#333a40;
  --muted:#6b7780;
  --line:#d9e1e6;
  --soft:#eef3f6;
  --field:#f4f6f8;
  --hero-a:#0d1c2a;
  --hero-b:#1c3a4f;
  --white:#ffffff;
}
*{box-sizing:border-box;margin:0;padding:0}
html,body{width:1200px;height:3836px;overflow:hidden}
body{font-family:"Open Sans",Arial,sans-serif;color:var(--ink);background:var(--white);font-size:13px;line-height:1.5}
.btn{display:inline-block;background:var(--accent);color:var(--white);font-family:"Montserrat",Arial,sans-serif;font-weight:700;font-size:12px;letter-spacing:.5px;text-transform:uppercase;padding:10px 22px;border-radius:3px}
.section-title{font-family:"Montserrat",Arial,sans-serif;font-weight:700;font-size:26px;color:var(--heading);text-align:center;text-transform:uppercase;letter-spacing:.5px}

/* hero */
.hero{position:relative;height:500px;background:linear-gradient(160deg,var(--hero-b),var(--hero-a) 70%);color:var(--white);text-align:center}
.nav{position:absolute;top:0;left:0;right:0;height:80px;display:flex;align-items:center;padding:0 60px}
.brand{display:flex;align-items:center;gap:10px;font-family:"Montserrat",Arial,sans-serif;font-weight:700;font-size:16px;color:var(--white);width:260px}
.brand-mark{width:14px;height:14px;background:var(--accent)}
.nav-links{display:flex;gap:34px;margin-left:auto;margin-right:40px;font-family:"Montserrat",Arial,sans-serif;font-size:11px;font-weight:600;text-transform:uppercase}
.nav-links .active{background:var(--accent);padding:8px 14px;border-radius:3px;margin:-8px -14px}
.nav .btn{padding:8px 16px;font-size:11px}
.hero-welcome{padding-top:168px;font-size:20px;font-weight:300}
.hero-title{font-family:"Montserrat",Arial,sans-serif;font-weight:600;font-size:42px;letter-spacing:1px;margin-top:4px}
.hero-text{width:720px;margin:14px auto 0;font-size:14px;line-height:1.6;color:#dbe6ee}
.hero .cta{margin-top:40px;padding:13px 34px}

/* rooms */
.rooms{height:1060px;padding-top:34px}
.room-grid{width:904px;margin:22px auto 0;display:grid;grid-template-columns:repeat(3,292px);gap:14px 14px}
.room-card{height:448px;background:var(--white);box-shadow:0 2px 8px rgba(0,0,0,.14);text-align:center}
.room-photo{height:200px}
.room-name{font-family:"Montserrat",Arial,sans-serif;font-weight:700;font-size:17px;margin-top:20px;text-transform:uppercase}
.room-desc{font-size:11.5px;color:var(--muted);padding:8px 24px 0;height:96px}
.room-meta{display:flex;justify-content:space-between;padding:10px 40px;font-size:11px;color:var(--muted);border-top:1px solid var(--line);margin:0 24px}
.room-card .btn{margin-top:14px;padding:9px 20px;font-size:11px}
.p-elevator{background:linear-gradient(135deg,#7a1d2b,#c24a4e)}
.p-speech{background:linear-gradient(135deg,#2f3f7a,#b7a16a)}
.p-heist{background:linear-gradient(135deg,#3a2a55,#7b5c8f)}
.p-jail{background:linear-gradient(135deg,#c86a2a,#e38b3c)}
.p-candy{background:linear-gradient(135deg,#b04a3e,#e3c6a8)}
.p-more{background:linear-gradient(135deg,#4f6f88,#c9a67c)}

/* events */
.events{height:760px;padding-top:36px;text-align:center}
.events-intro{width:720px;margin:20px auto 0;font-size:13px;color:var(--muted)}
.event-types{width:900px;margin:30px auto 0;display:flex;justify-content:space-between;padding:0 36px}
.event{width:160px}
.event-ring{width:160px;height:160px;border-radius:50%;border:4px solid var(--accent);display:flex;align-items:center;justify-content:center}
.event-art{width:92px;height:92px;border-radius:50%}
.a-corp{background:radial-gradient(circle,#e43c45,#f28b8f)}
.a-bday{background:radial-gradient(circle,#f4a9c4,#f7d7e3)}
.a-anniv{background:radial-gradient(circle,#f5c040,#61b4e4)}
.a-holiday{background:radial-gradient(circle,#f0a52c,#e0464a)}
.event-label{font-family:"Montserrat",Arial,sans-serif;font-weight:700;font-size:12px;margin-top:14px;text-transform:uppercase}
.form{width:904px;margin:0 auto;display:grid;grid-template-columns:444px 444px;gap:16px;text-align:left}
.events .form{margin-top:48px}
.fields{display:flex;flex-direction:column;gap:6px}
.field{height:33px;background:var(--field);border:1px solid var(--line);font-size:11px;color:var(--muted);padding:8px 12px}
.field.area{height:100%}
.events .btn,.contact .btn{margin-top:28px;padding:10px 24px;font-size:11px}

/* how it works */
.how{height:800px;background:var(--soft);padding-top:30px}
.faq-grid{width:904px;margin:28px auto 0;display:grid;grid-template-columns:repeat(3,292px);grid-auto-rows:140px;gap:14px}
.faq{background:var(--white);box-shadow:0 1px 5px rgba(0,0,0,.1);padding:18px 20px;text-align:center}
.faq h3{font-family:"Montserrat",Arial,sans-serif;font-weight:700;font-size:13.5px;color:var(--ink);line-height:1.35}
.faq p{font-size:11px;color:var(--muted);margin-top:8px}
.faq a{color:var(--accent);font-weight:700;text-decoration:none}

/* location */
.location{height:344px;padding-top:50px}
.loc-body{width:904px;margin:24px auto 0;display:flex;align-items:flex-start}
.map{width:480px;height:210px;margin-left:110px;background:linear-gradient(135deg,#e8ecef,#d7e3d2 55%,#e6e1cf)}
.loc-info{margin-left:auto;width:260px;text-align:center;font-size:12px;color:var(--muted)}
.loc-info h4{font-family:"Montserrat",Arial,sans-serif;font-size:13px;color:var(--ink);margin-top:12px}
.loc-info h4:first-child{margin-top:0}

/* contact */
.contact{height:372px;background:var(--soft);padding-top:22px;text-align:center;position:relative}
.contact-line{font-size:13px;margin-top:6px}
.contact-line b{color:var(--accent)}
.contact .form{margin-top:18px;width:904px}
.contact .fields{gap:8px}
.footer{position:absolute;left:60px;right:60px;bottom:10px;display:flex;justify-content:space-between;align-items:center;font-size:10px;color:var(--muted)}
.social{display:flex;gap:6px}
.social span{width:18px;height:18px;border-radius:50%;background:var(--accent)}
</style>
</head>
<body>

<header class="hero" role="img" aria-label="Dimly lit escape room interior behind the welcome message">
  <nav class="nav">
    <div class="brand"><span class="brand-mark"></span>Puzzle Vault Larkfield</div>
    <div class="nav-links">
      <span class="active">Escape Rooms</span><span>Special Events</span><span>How It Works</span><span>Location</span><span>Contact Us</span>
    </div>
    <span class="btn">Book Now</span>
  </nav>
  <p class="hero-welcome">Welcome to</p>
  <h1 class="hero-title">PUZZLE VAULT LARKFIELD</h1>
  <p class="hero-text">Experience this fascinating, exciting &amp; thrilling entertainment! Cracking codes, discovering clues, and solving puzzles, you will find your ingenuity. Bring your friends and family together, and enjoy the adventure.</p>
  <span class="btn cta">Book Now</span>
</header>

<section class="rooms">
  <h2 class="section-title">Choose Your Own Escape Room</h2>
  <div class="room-grid">
    <article class="room-card">
      <div class="room-photo p-elevator" role="img" aria-label="Players inside the red-lit elevator room"></div>
      <h3 class="room-name">Elevator</h3>
      <p class="room-desc">The steel elevator has jammed between floors. Work together to find the override code and reset the panel before the cables give way and time runs out.</p>
      <div class="room-meta"><span>$28.00/person</span><span>Min 2 Max 8</span></div>
      <span class="btn">Book Now</span>
    </article>
    <article class="room-card">
      <div class="room-photo p-speech" role="img" aria-label="Presidential seal and podium in the speech room"></div>
      <h3 class="room-name">The Speech</h3>
      <p class="room-desc">The President's speech has been hijacked and replaced with a fake one. In one hour, the nation will hear it. Find the real speech before the clock runs out.</p>
      <div class="room-meta"><span>$28.00/person</span><span>Min 2 Max 8</span></div>
      <span class="btn">Book Now</span>
    </article>
    <article class="room-card">
      <div class="room-photo p-heist" role="img" aria-label="Vault door and safe in the bank heist room"></div>
      <h3 class="room-name">Bank Heist</h3>
      <p class="room-desc">With your skills and teamwork, crack the vault and escape with the diamonds before the alarm sounds and the guards lock every exit down for good.</p>
      <div class="room-meta"><span>$28.00/person</span><span>Min 2 Max 8</span></div>
      <span class="btn">Book Now</span>
    </article>
    <article class="room-card">
      <div class="room-photo p-jail" role="img" aria-label="Group in orange jumpsuits in the jail break room"></div>
      <h3 class="room-name">Jail Break</h3>
      <p class="room-desc">Framed for a crime you did not commit, you have one hour while the guard is away to pick the locks and break out.</p>
      <div class="room-meta"><span>$28.00/person</span><span>Min 2 Max 8</span></div>
      <span class="btn">Book Now</span>
    </article>
    <article class="room-card">
      <div class="room-photo p-candy" role="img" aria-label="Colourful candy shop counter and shelves"></div>
      <h3 class="room-name">Candy Shop</h3>
      <p class="room-desc">With all of the candy right before your eyes, find the golden ticket and win the prize before the shop closes.</p>
      <div class="room-meta"><span>$28.00/person</span><span>Min 2 Max 8</span></div>
      <span class="btn">Book Now</span>
    </article>
    <article class="room-card">
      <div class="room-photo p-more" role="img" aria-label="Happy group of players after an escape"></div>
      <h3 class="room-name">More to Come</h3>
      <p class="room-desc">Visit our website regularly and we will update our rooms in the future. Also, ask any one of our game masters.</p>
      <div class="room-meta"><span>$28.00/person</span><span>Min 2 Max 8</span></div>
      <span class="btn">Book Now</span>
    </article>
  </div>
</section>

<section class="events">
  <h2 class="section-title">Special Events</h2>
  <p class="events-intro">Puzzle Vault Larkfield is the perfect place to gather groups of colleagues, friends or family and experience the latest entertainment in town. Simply complete the form below and our specialist will contact you for further details. Group pricing is available to groups parties.</p>
  <div class="event-types">
    <div class="event"><div class="event-ring"><div class="event-art a-corp" role="img" aria-label="Heart icon"></div></div><p class="event-label">Corporate Meetings</p></div>
    <div class="event"><div class="event-ring"><div class="event-art a-bday" role="img" aria-label="Birthday cake icon"></div></div><p class="event-label">Birthday Parties</p></div>
    <div class="event"><div class="event-ring"><div class="event-art a-anniv" role="img" aria-label="Balloons icon"></div></div><p class="event-label">Anniversaries</p></div>
    <div class="event"><div class="event-ring"><div class="event-art a-holiday" role="img" aria-label="Party hat icon"></div></div><p class="event-label">Holidays</p></div>
  </div>
  <form class="form">
    <div class="fields">
      <div class="field">Your Name *</div>
      <div class="field">Company Name</div>
      <div class="field">Your Email *</div>
      <div class="field">Your Phone *</div>
      <div class="field">Date of Party</div>
      <div class="field">Guest Number *</div>
    </div>
    <div class="field area">Your Message *</div>
  </form>
  <span class="btn">Send Message</span>
</section>

<section class="how">
  <h2 class="section-title">How It Works</h2>
  <div class="faq-grid">
    <div class="faq"><h3>How do I make a reservation?</h3><p>Click on the Book now button or click here.<br><a>Book Now</a></p></div>
    <div class="faq"><h3>How long does an escape last?</h3><p>Each escape lasts 60 minutes.</p></div>
    <div class="faq"><h3>Is there an age limit?</h3><p>Participants 12 and older can play by themselves as long as an adult signs the waiver. Under 12 must be with an adult.</p></div>
    <div class="faq"><h3>I'm pregnant, can I participate?</h3><p>Sure, there is no risk to you.</p></div>
    <div class="faq"><h3>How can I redeem a voucher or promo code?</h3><p>Click on the Book now button and enter the code in the promo code area box.</p></div>
    <div class="faq"><h3>Where do I park?</h3><p>Plenty of parking in front of the building.</p></div>
    <div class="faq"><h3>Do I have to sign a liability waiver?</h3><p>Yes. You can find the liability waiver here.<br><a>Click here for waiver</a></p></div>
    <div class="faq"><h3>Which room is the most challenging?</h3><p>They are all challenging!</p></div>
    <div class="faq"><h3>What is the cancellation policy?</h3><p>All hours online from the scheduled reservation date. If you don't cancel within 24 hours you will lose your reservation and payment.</p></div>
    <div class="faq"><h3>What time should we arrive?</h3><p>Please arrive 15 minutes early.<br><a>Find out more</a></p></div>
  </div>
</section>

<section class="location">
  <h2 class="section-title">Location</h2>
  <div class="loc-body">
    <div class="map" role="img" aria-label="Street map showing the venue location"></div>
    <div class="loc-info">
      <h4>ADDRESS</h4>
      <p>1200 Larkfield Commons Drive, Suite 200<br>Larkfield, VA 20100</p>
      <h4>PHONE NUMBER</h4>
      <p>(555) 014-2604</p>
      <h4>HOURS</h4>
      <p>Wednesday – Friday : 4pm – 10pm<br>Saturday : 11am – 11pm<br>Sunday : 11am – 9:30pm</p>
    </div>
  </div>
</section>

<section class="contact">
  <h2 class="section-title">Contact Us</h2>
  <p class="contact-line">Call <b>555 014 2604</b> or Send a Message</p>
  <form class="form">
    <div class="fields">
      <div class="field">Your Name</div>
      <div class="field">Your Email</div>
      <div class="field">Your Phone</div>
    </div>
    <div class="field area">We'd love to hear from you! We'll get back to you immediately</div>
  </form>
  <span class="btn">Submit</span>
  <footer class="footer">
    <span>Copyright © Puzzle Vault Larkfield</span>
    <div class="social"><span></span><span></span><span></span><span></span></div>
  </footer>
</section>

</body>
</html>
```